Roofing Contractor business card redesign

I want to redesign my business card with a fresh, eye catching concept

Target Market(s)

Residential Roofing Clients, potential employees, and subcontractors.

Industry/Entity Type

Business

Colors

Designer to choose colors to be used in the design.

Requirements
Nice to have
• I just want something that's more pleasing to the eye. You can use a combination of either / or of my logos.

```html
<!DOCTYPE html>
<html lang="en">
<head>
<meta charset="utf-8">
<title>Fair Hand General Contractors – Business Card</title>
<link href="https://fonts.googleapis.com/css2?family=Oswald:wght@400;500;600&family=Source+Sans+3:wght@400;600&display=swap" rel="stylesheet">
<style>
  :root {
    --stage: #0f0f0f;
    --card-light: #ececec;
    --card-dark: #4b150f;
    --brand-brown: #4a1310;
    --accent-orange: #e0691c;
    --body-text: #333333;
    --white: #ffffff;
  }
  * { margin: 0; padding: 0; box-sizing: border-box; }
  html, body { width: 1200px; height: 900px; overflow: hidden; background: var(--stage); }
  .stage { position: relative; width: 1200px; height: 900px; }

  .card { position: absolute; top: 170px; width: 347px; height: 561px; }
  .card-front { left: 259px; background: var(--card-light); }
  .card-back { left: 631px; background: var(--card-dark); overflow: hidden; }

  .brand { position: absolute; left: 0; width: 100%; text-align: center;
    font-family: "Oswald", sans-serif; font-weight: 600; }
  .brand-name { display: flex; justify-content: center; align-items: center; gap: 10px; line-height: 1; }
  .brand-mark { display: inline-block; border-radius: 50%; }
  .brand-sub { line-height: 1; margin-top: 8px; }

  .card-front .brand { top: 120px; color: var(--brand-brown); }
  .card-front .brand-name { font-size: 46px; }
  .card-front .brand-mark { width: 50px; height: 50px; background: var(--brand-brown); }
  .card-front .brand-sub { font-size: 19px; letter-spacing: 0.3px; }

  .card-back .brand { top: 226px; color: var(--white); }
  .card-back .brand-name { font-size: 52px; }
  .card-back .brand-mark { width: 60px; height: 60px; background: var(--white); }
  .card-back .brand-sub { font-size: 22px; letter-spacing: 0.3px; }

  .back-art { position: absolute; inset: 0; }

  .contact-block { position: absolute; left: 0; top: 284px; width: 100%; text-align: center;
    font-family: "Source Sans 3", sans-serif; color: var(--body-text); font-size: 15.5px; line-height: 20.5px; }
  .person-name { font-family: "Oswald", sans-serif; font-weight: 400; font-size: 26px;
    color: var(--brand-brown); line-height: 1.2; margin-bottom: 4px; }
  .divider { width: 156px; height: 1px; background: var(--brand-brown); margin: 10px auto 13px; }
  .label { color: var(--accent-orange); font-weight: 600; }
  .web { color: var(--accent-orange); }
  .address { margin-top: 16px; }
</style>
</head>
<body>
<main class="stage">
  <section class="card card-front" aria-label="Card front">
    <div class="brand">
      <div class="brand-name">Fair <span class="brand-mark"></span> Hand</div>
      <div class="brand-sub">General Contractors, Inc.</div>
    </div>
    <div class="contact-block">
      <p class="person-name">Dale Merrick</p>
      <p>Ridgeline certified Roof Inspector</p>
      <p>Licensed Property Adjuster</p>
      <div class="divider"></div>
      <p><span class="label">P:</span> (555) 214-3080</p>
      <p><span class="label">M:</span> (555) 318-7742</p>
      <p><span class="label">E:</span> dale@fairhandtx.com</p>
      <p class="web">www.FairHandGC.com</p>
      <p class="address">4810 Cedar Ridge Drive Suite 110<br>Austin, TX 78701</p>
    </div>
  </section>

  <section class="card card-back" aria-label="Card back">
    <svg class="back-art" width="347" height="561" viewBox="0 0 347 561" role="img"
         aria-label="Faint tone-on-tone illustration of the contractor crew behind the logo">
      <defs>
        <radialGradient id="backGlow" cx="50%" cy="45%" r="70%">
          <stop offset="0%" stop-color="#5a1d16"/>
          <stop offset="100%" stop-color="#47130e"/>
        </radialGradient>
      </defs>
      <rect width="347" height="561" fill="url(#backGlow)"/>
    </svg>
    <div class="brand">
      <div class="brand-name">Fair <span class="brand-mark"></span> Hand</div>
      <div class="brand-sub">General Contractors, Inc.</div>
    </div>
  </section>
</main>
</body>
</html>
```